Brightwave Reach - Business Card

We need a business card for a Social Media Marketing company that specializes in online marketing for small businesses in Canada using common Social Media platforms such as Pixlora, Chatterly, Blinkpost & Quibber.

I have uploaded a copy of our logo which I would like utilized in the business card. We would like the business card to be modern yet classy design.

Our website is www.brightwavereach.ca

Industry/Entity Type

Marketing

Contact Information for Business Card

Email: info@brightwavereach.ca
Website: www.brightwavereach.ca
Telephone: 604-555-0193

Colors

Designer to choose colors to be used in the design.

Requirements
Must have
• Social Media icons on reverse
• Please add some designs with color.

```html
<!DOCTYPE html>
<html lang="en">
<head>
<meta charset="utf-8">
<title>Brightwave Reach – Business Card</title>
<link href="https://fonts.googleapis.com/css2?family=Open+Sans:wght@400;700;800&display=swap" rel="stylesheet">
<style>
  :root {
    --page: #e6e7e8;
    --card-dark: #363b3d;
    --card-light: #ffffff;
    --ink: #2f3335;
    --ink-soft: #8a8f92;
    --on-dark: #e9ebec;
    --on-dark-soft: #b9bec1;
  }
  * { box-sizing: border-box; margin: 0; padding: 0; }
  html, body { width: 1200px; height: 960px; overflow: hidden; }
  body {
    background: var(--page);
    font-family: "Open Sans", Arial, sans-serif;
    position: relative;
  }
  .card {
    position: absolute;
    width: 700px;
    height: 400px;
    border-radius: 4px;
    box-shadow: 0 10px 30px rgba(0,0,0,0.18);
    overflow: hidden;
  }
  /* Reverse side */
  .card-back {
    left: 300px; top: 50px;
    background: var(--card-dark);
    color: var(--on-dark);
  }
  .back-brand {
    position: absolute;
    left: 0; right: 0; top: 130px;
    display: flex; align-items: center; justify-content: center; gap: 14px;
  }
  .brand-square {
    width: 22px; height: 22px;
    background: currentColor;
  }
  .brand-name {
    font-weight: 800;
    font-size: 40px;
    letter-spacing: 1px;
    text-transform: uppercase;
    line-height: 1;
  }
  .social-list {
    position: absolute;
    left: 0; right: 0; top: 300px;
    display: flex; justify-content: center; gap: 28px;
    list-style: none;
    font-size: 15px;
    color: var(--on-dark-soft);
  }
  .social-list li { display: flex; align-items: center; gap: 8px; }
  .social-dot {
    width: 10px; height: 10px; border-radius: 50%;
    border: 1.5px solid var(--on-dark-soft);
  }
  /* Front side */
  .card-front {
    left: 200px; top: 510px;
    background: var(--card-light);
    color: var(--ink);
  }
  .edge-tab {
    position: absolute;
    left: 0; top: 0;
    width: 16px; height: 200px;
    background: var(--card-dark);
  }
  .contact-block {
    position: absolute;
    left: 50px; top: 160px;
  }
  .person-name {
    font-weight: 700;
    font-size: 20px;
    text-transform: uppercase;
    letter-spacing: 0.5px;
  }
  .person-role {
    font-size: 16px;
    color: var(--ink-soft);
    text-transform: uppercase;
    margin-bottom: 18px;
  }
  .contact-list { list-style: none; font-size: 17px; }
  .contact-list li {
    display: flex; align-items: center; gap: 12px;
    line-height: 28px;
  }
  .contact-icon { width: 14px; height: 14px; fill: var(--ink); flex: none; }
  .front-brand {
    position: absolute;
    right: 60px; top: 110px;
    display: flex; align-items: center; gap: 12px;
    color: var(--ink);
  }
  .front-brand .brand-name { font-size: 32px; }
  .front-brand .brand-square { width: 18px; height: 18px; }
</style>
</head>
<body>
  <section class="card card-back" aria-label="Business card reverse">
    <div class="back-brand">
      <span class="brand-square"></span>
      <span class="brand-name">Brightwave Reach</span>
    </div>
    <ul class="social-list">
      <li><span class="social-dot"></span>Chatterly</li>
      <li><span class="social-dot"></span>Pixlora</li>
      <li><span class="social-dot"></span>Quibber</li>
    </ul>
  </section>

  <section class="card card-front" aria-label="Business card front">
    <div class="edge-tab"></div>
    <div class="contact-block">
      <p class="person-name">Evan Hartley</p>
      <p class="person-role">CEO/Founder</p>
      <ul class="contact-list">
        <li>
          <svg class="contact-icon" viewBox="0 0 16 16" aria-hidden="true"><path d="M3 1h3l1 4-2 1a9 9 0 0 0 5 5l1-2 4 1v3a2 2 0 0 1-2 2A13 13 0 0 1 1 3a2 2 0 0 1 2-2z"/></svg>
          604-555-0193
        </li>
        <li>
          <svg class="contact-icon" viewBox="0 0 16 16" aria-hidden="true"><path d="M1 3h14v10H1z M1 3l7 6 7-6" /></svg>
          info@brightwavereach.ca
        </li>
        <li>
          <svg class="contact-icon" viewBox="0 0 16 16" aria-hidden="true"><circle cx="8" cy="8" r="7"/></svg>
          www.brightwavereach.ca
        </li>
      </ul>
    </div>
    <div class="front-brand">
      <span class="brand-square"></span>
      <span class="brand-name">Brightwave Reach</span>
    </div>
  </section>
</body>
</html>
```